A Spin Above Par Company Brochure

I am the owner of a Mobile Disc Jockey company specializing in weddings. I am looking for a Tri Fold color brochure that is modern and eye catching with the focus being on upscale wedding events. I also want it to be easy to read and not overly cluttered ! I would like it to reflect our website located at aspinabovepar.example
I also have different variations and file types of my logo such as jpeg and png files. I need some good dance floor pics. If you do not have any good stock photos I can look through my photo library. I uploaded a logo and pic I found from one of my videos. Not sure if it is worth anything.
We also do Uplighting and Photo Booths which I would like in the brochure. Much of the text copy needed can be taken from our website if needed. Please refer to the website to see what we do and our style.

Target Market(s)

upscale weddings

Industry/Entity Type

wedding dj entertainment & masters of ceremonies

Requirements
Nice to have
• nice pictures of packed dance floors and people having fun

```html
<!DOCTYPE html>
<html lang="en">
<head>
<meta charset="utf-8">
<title>A Spin Above Par — Tri-Fold Brochure</title>
<link href="https://fonts.googleapis.com/css2?family=Bitter:wght@500;700;800&family=Montserrat:wght@400;500;700;800&display=swap" rel="stylesheet">
<style>
  :root {
    --backdrop: #e9e6ea;
    --purple: #6a2277;
    --purple-deep: #4b1656;
    --purple-bright: #8a3a9e;
    --accent-red: #c4153f;
    --paper: #ffffff;
    --ink-grey: #6f6f72;
    --photo-dark: #1c0f2a;
    --photo-glow: #b0204a;
  }
  * { box-sizing: border-box; margin: 0; padding: 0; }
  html, body {
    width: 1200px; height: 800px; overflow: hidden;
    background: var(--backdrop);
  }
  .brochure {
    position: absolute; left: 105px; top: 30px;
    width: 990px; height: 740px;
    display: flex;
    box-shadow: 0 12px 30px rgba(40, 10, 50, 0.18);
  }
  .panel { position: relative; width: 330px; height: 100%; overflow: hidden; }

  /* Left panel */
  .panel--services { background: linear-gradient(180deg, var(--purple) 0%, var(--purple-deep) 100%); }
  .accent-square {
    position: absolute; width: 28px; height: 28px; background: var(--accent-red);
  }
  .panel--services .accent-square--top { left: 20px; top: 22px; }
  .panel--services .accent-square--mid { left: 20px; top: 377px; }
  .services-list {
    position: absolute; left: 47px; top: 148px; width: 270px;
    font-family: 'Bitter', serif; font-weight: 700;
    font-size: 22px; line-height: 1.35; color: var(--paper);
  }
  .photo {
    position: absolute;
    background: radial-gradient(ellipse at 55% 70%, var(--photo-glow) 0%, #5a1846 35%, var(--photo-dark) 75%);
  }
  .panel--services .photo { left: 0; bottom: 0; width: 100%; height: 205px; }
  .energy-tag {
    position: absolute; left: 10px; bottom: 28px;
    font-family: 'Montserrat', sans-serif; font-weight: 800; color: var(--paper);
  }
  .energy-tag__lead { display: block; font-size: 13px; letter-spacing: 0.5px; }
  .energy-tag__word {
    display: inline-block; margin-top: 2px; padding: 1px 5px;
    background: var(--paper); color: var(--purple);
    font-size: 19px; letter-spacing: 4px;
  }

  /* Centre panel */
  .panel--cover { background: var(--paper); }
  .brand-name {
    position: absolute; left: 24px; top: 78px;
    display: flex; align-items: center; gap: 10px;
    font-family: 'Bitter', serif; font-weight: 700; font-size: 27px;
    color: var(--ink-grey);
  }
  .brand-name__dot {
    width: 18px; height: 18px; border-radius: 50%; background: var(--purple-bright);
    flex: none;
  }
  .tagline {
    position: absolute; left: 20px; top: 185px; width: 300px;
    font-family: 'Bitter', serif; font-weight: 800; font-size: 16px;
    line-height: 1.35; color: var(--purple-bright); text-transform: uppercase;
  }
  .headline {
    position: absolute; left: 14px; top: 268px; width: 310px;
    font-family: 'Bitter', serif; font-weight: 800; font-size: 35px;
    line-height: 1.25; color: var(--ink-grey);
  }
  .headline__em { color: var(--purple); }
  .band {
    position: absolute; left: 0; top: 530px; width: 100%; height: 28px;
    background: linear-gradient(90deg, var(--purple-deep), var(--purple-bright));
  }
  .contact {
    position: absolute; left: 18px; top: 585px;
    font-family: 'Montserrat', sans-serif; font-weight: 500; font-size: 19px;
    line-height: 1.3; color: var(--ink-grey); font-style: normal;
  }

  /* Right panel */
  .panel--promise { background: linear-gradient(180deg, var(--purple-deep) 0%, var(--purple) 55%, var(--purple-deep) 100%); }
  .panel--promise .accent-square--top { right: 14px; top: 26px; }
  .promise {
    position: absolute; left: 36px; top: 160px; width: 290px;
    font-family: 'Bitter', serif; font-weight: 700; font-size: 33px;
    line-height: 1.42; color: var(--paper); z-index: 2;
  }
  .panel--promise .photo { right: 0; top: 330px; width: 168px; height: 410px; }
  .footer-name {
    position: absolute; left: 18px; bottom: 50px; width: 130px;
    display: flex; align-items: center; gap: 8px;
    font-family: 'Bitter', serif; font-weight: 700; font-size: 15px;
    line-height: 1.2; color: var(--paper);
  }
  .footer-name__dot {
    width: 12px; height: 12px; border-radius: 50%; background: var(--paper); flex: none;
  }
</style>
</head>
<body>
  <main class="brochure">
    <section class="panel panel--services">
      <span class="accent-square accent-square--top"></span>
      <span class="accent-square accent-square--mid"></span>
      <p class="services-list">Weddings,<br>Corporate Events,<br>Private Parties,<br>any event is better<br>with A Spin Above Par</p>
      <div class="photo" role="img" aria-label="Close-up of a DJ's hand on a mixing console lit in purple and red"></div>
      <p class="energy-tag"><span class="energy-tag__lead">WE BRING THE</span><span class="energy-tag__word">ENERGY</span></p>
    </section>

    <section class="panel panel--cover">
      <p class="brand-name"><span class="brand-name__dot"></span>A Spin Above Par</p>
      <p class="tagline">The most recommended<br>DJ’s in Southwest Florida</p>
      <h1 class="headline">It’s your day.<br><span class="headline__em">Let us help you<br>make it happen,</span><br>your way</h1>
      <div class="band"></div>
      <address class="contact">A Spin Above Par<br>Palm Harbor Cove, FL 30000<br>555.014.2290<br>hello@aspinabovepar.example</address>
    </section>

    <section class="panel panel--promise">
      <span class="accent-square accent-square--top"></span>
      <p class="promise">Modern,<br>Tasteful,<br>&amp; Fun<br>Entertainment</p>
      <div class="photo" role="img" aria-label="DJ turntable and mixer glowing red under party lights"></div>
      <p class="footer-name"><span class="footer-name__dot"></span>A Spin Above Par</p>
    </section>
  </main>
</body>
</html>
```